Business Card Design For A Renovation Contractor Company

We need a business card for a new company based in Singapore, our company name is "RB Tolvane". We are a renovation contractor that builds designs into reality. We build more of F&B restaurants, retail stores and commercial offices. We work very closely with designers. The final design should communicate to our client that we are a company that you can trust, that will plan and complete your project without giving you a headache. I like my client to remember my company as "RB". The beauty of SIMPLE is important.

Industry/Entity Type

Contractor

Requirements
Nice to have
• Black or Red base

```html
<!DOCTYPE html>
<html lang="en">
<head>
<meta charset="utf-8">
<title>RB Tolvane – Business Card</title>
<link href="https://fonts.googleapis.com/css2?family=Arimo:wght@400;700&display=swap" rel="stylesheet">
<style>
  :root {
    --page-bg: #e4e4ea;
    --card-bg: #ffffff;
    --ink: #1a1a1a;
    --ink-soft: #444444;
    --brand-red: #e3202a;
    --rule: #9a9a9a;
  }
  * { box-sizing: border-box; margin: 0; padding: 0; }
  html, body {
    width: 1200px; height: 987px; overflow: hidden;
    background: var(--page-bg);
    font-family: "Arimo", Arial, sans-serif;
    color: var(--ink);
  }
  .stage {
    position: relative; width: 1200px; height: 987px;
    display: flex; align-items: center; justify-content: center; gap: 44px;
  }
  .card {
    position: relative; width: 540px; height: 309px;
    background: var(--card-bg); border-radius: 26px; overflow: hidden;
    box-shadow: 0 6px 18px rgba(0,0,0,.12);
  }

  /* Front */
  .card-front .swoosh { position: absolute; left: 0; bottom: 0; width: 540px; height: 309px; }
  .brand-block { position: absolute; left: 200px; top: 26px; width: 300px; }
  .brand-line { display: flex; align-items: center; gap: 10px; }
  .brand-dot { width: 34px; height: 34px; border-radius: 50%; background: var(--ink); flex: none; }
  .brand-name { font-size: 40px; font-weight: 400; color: var(--ink); letter-spacing: -0.5px; line-height: 1; }
  .brand-rule { height: 1px; background: var(--ink); margin: 6px 0 3px; }
  .tagline { font-size: 16px; color: var(--ink); letter-spacing: 0.3px; }

  .person { position: absolute; left: 70px; top: 140px; width: 190px; text-align: right; }
  .person-name { font-size: 22px; font-weight: 700; color: var(--brand-red); }
  .person-title { font-size: 15px; color: var(--ink-soft); margin-bottom: 6px; }
  .person-address { font-size: 14px; color: var(--ink-soft); line-height: 1.35; }

  .divider { position: absolute; left: 276px; top: 140px; width: 1px; height: 110px;
    background: linear-gradient(var(--card-bg), var(--rule), var(--card-bg)); }

  .contact { position: absolute; left: 292px; top: 146px; list-style: none; }
  .contact li { font-size: 15px; color: var(--ink-soft); line-height: 1.5; }
  .contact .label { color: var(--brand-red); display: inline-block; width: 20px; }

  /* Back */
  .card-back { display: flex; flex-direction: column; align-items: center; justify-content: center; gap: 30px; }
  .back-mark { display: flex; align-items: center; gap: 14px; }
  .back-mark .brand-dot { width: 56px; height: 56px; }
  .back-mark .brand-name { font-size: 58px; }
  .web { font-size: 17px; letter-spacing: 5px; color: var(--ink-soft); }
  .web .accent { color: var(--brand-red); }
</style>
</head>
<body>
<main class="stage">
  <section class="card card-front" aria-label="Business card front">
    <svg class="swoosh" viewBox="0 0 540 309" preserveAspectRatio="none" aria-hidden="true">
      <path d="M0 180 C60 200 90 260 170 280 C240 298 330 300 420 309 L0 309 Z" fill="#1a1a1a"/>
      <path d="M0 196 C60 214 100 268 180 288 C250 302 330 304 400 309 L0 309 Z" fill="#ffffff"/>
      <path d="M0 206 C60 226 110 276 190 294 C260 306 320 307 370 309 L0 309 Z" fill="#e3202a"/>
    </svg>

    <div class="brand-block">
      <div class="brand-line">
        <span class="brand-dot"></span>
        <span class="brand-name">RB Tolvane</span>
      </div>
      <div class="brand-rule"></div>
      <p class="tagline">planned well, built to last</p>
    </div>

    <div class="person">
      <p class="person-name">Your Name</p>
      <p class="person-title">Title</p>
      <p class="person-address">Door No. Street Name<br>City Name, State, Zip Code</p>
    </div>

    <div class="divider"></div>

    <ul class="contact">
      <li><span class="label">p:</span> 123-456-7890</li>
      <li><span class="label">c:</span> 123-456-7890</li>
      <li><span class="label">e:</span> info@rbtolvane.com</li>
      <li><span class="label">w:</span> www.rbtolvane.com</li>
    </ul>
  </section>

  <section class="card card-back" aria-label="Business card back">
    <div class="back-mark">
      <span class="brand-dot"></span>
      <span class="brand-name">RB Tolvane</span>
    </div>
    <p class="web">www.<span>rb</span><span class="accent">tolvane</span>.com</p>
  </section>
</main>
</body>
</html>
```